Brantor Works Business Card

Modern and Professional Business Card for a Med size construction/development company.

See the samples below for the design I like … but I need ideas for incorporating the red company logo while still keeping the clean look of the card samples that are attached.

Logo and tag line on the back … info on the front.

Tagline: Built Right from the First Footing

Target Market(s)

Med-Large General Contractors

Contact Information for Business Card

Brantor Works Limited
42 Fenwick Avenue
Mt. Pearl, NL
A1N 4R9

t: 709-555-0147
f: 709-555-0182
w: www.brantorworks-example.com

Font styles to use
Sans Serif

Colors
fbee3e

Requirements
Must have
• I like the black and yellow designs of the attached samples …. but I'm not sure how to incorporate the red Brantor Works logo into that design??
Nice to have
• Construction safety strips

```html
<!DOCTYPE html>
<html lang="en">
<head>
<meta charset="utf-8">
<title>Brantor Works Business Card</title>
<link href="https://fonts.googleapis.com/css2?family=Jost:wght@400;600&display=swap" rel="stylesheet">
<style>
  :root {
    --stage: #2a2a2b;
    --card: #0a0a0b;
    --yellow: #fbee3e;
    --red: #e8202a;
    --white: #f4f4f4;
  }
  * { box-sizing: border-box; margin: 0; padding: 0; }
  html, body { width: 1200px; height: 900px; overflow: hidden; }
  body {
    background: var(--stage);
    font-family: "Jost", sans-serif;
    position: relative;
  }
  .card {
    position: absolute;
    left: 320px;
    width: 560px;
    height: 320px;
    background: var(--card);
    border-radius: 22px;
    overflow: hidden;
  }
  .card--back { top: 100px; }
  .card--front { top: 470px; }

  /* brand name block */
  .brand {
    display: flex;
    align-items: center;
    gap: 12px;
  }
  .brand__square {
    width: 26px; height: 26px;
    background: var(--red);
    border-radius: 4px;
    flex: none;
  }
  .brand__name {
    color: var(--white);
    font-weight: 600;
    letter-spacing: 0.04em;
    text-transform: uppercase;
    white-space: nowrap;
  }

  /* back */
  .card--back .brand {
    position: absolute;
    top: 112px; left: 0; right: 0;
    justify-content: center;
  }
  .card--back .brand__name { font-size: 36px; }
  .tagline {
    position: absolute;
    top: 208px; left: 0; right: 0;
    text-align: center;
    color: var(--yellow);
    font-size: 16px;
    letter-spacing: 0.03em;
  }

  /* front */
  .card--front .brand {
    position: absolute;
    top: 38px; left: 40px;
  }
  .card--front .brand__square { width: 22px; height: 22px; }
  .card--front .brand__name { font-size: 26px; }
  .company {
    position: absolute;
    top: 104px; left: 40px;
    color: var(--yellow);
    font-weight: 600;
    font-size: 23px;
    white-space: nowrap;
  }
  .rule {
    position: absolute;
    top: 146px; left: 30px;
    width: 500px; height: 2px;
    background: var(--yellow);
  }
  .contacts {
    position: absolute;
    top: 164px; left: 40px;
    list-style: none;
    color: var(--white);
    font-size: 16px;
    line-height: 25px;
  }
  .contacts li { display: flex; align-items: center; gap: 10px; white-space: nowrap; }
  .contacts svg { width: 13px; height: 13px; fill: var(--yellow); flex: none; }
  .contacts .accent { color: var(--yellow); }
  .address {
    position: absolute;
    right: 40px; bottom: 28px;
    text-align: right;
    color: var(--white);
    font-size: 16px;
    font-style: normal;
    line-height: 22px;
    letter-spacing: 0.02em;
    white-space: nowrap;
  }
</style>
</head>
<body>

  <section class="card card--back">
    <div class="brand">
      <span class="brand__square"></span>
      <span class="brand__name">Brantor Works</span>
    </div>
    <p class="tagline">Built Right from the First Footing</p>
  </section>

  <section class="card card--front">
    <div class="brand">
      <span class="brand__square"></span>
      <span class="brand__name">Brantor Works</span>
    </div>
    <h1 class="company">Brantor Works Limited</h1>
    <div class="rule"></div>
    <ul class="contacts">
      <li>
        <svg viewBox="0 0 16 16" aria-hidden="true"><path d="M3.5 1l2.5 3-1.5 2c1 2 3 4 5 5l2-1.5 3 2.5-1.5 2.5C8 16 0 8 1 2.5z"/></svg>
        709-555-0147
      </li>
      <li>
        <svg viewBox="0 0 16 16" aria-hidden="true"><path d="M4 1h8v4H4zM1 6h14v6h-3v3H4v-3H1zM5 10v4h6v-4z"/></svg>
        709-555-0182
      </li>
      <li>
        <svg viewBox="0 0 16 16" aria-hidden="true"><path d="M1 3h14v10H1zM2.5 4.5L8 9l5.5-4.5v-.2H2.5z"/></svg>
        info@brantorworks-example.com
      </li>
      <li>
        <svg viewBox="0 0 16 16" aria-hidden="true"><circle cx="8" cy="8" r="7"/></svg>
        <span>www.<span class="accent">brantorworks-example</span>.com</span>
      </li>
    </ul>
    <address class="address">
      42 Fenwick Avenue<br>
      Kelby Cove, NL A9Z 0X5
    </address>
  </section>

</body>
</html>
```